Halvex Power

We need a business card for "Halvex power". I have uploaded the logo, the color of the card should be according to the logo "Blackish".
Basically halvex power is a solar company.
Also we would like a sample file in which we can edit the information such names and contact details ourselves
The card would be two sided with following details
1- logo on front and underneath the logo there should be a line saying
"Cleaner . Cheaper . Power"
2-website i.e "www.halvexpowerco.com"
3- Icons for Facebook and Instagram that tells the clients we are available on both social sites.
4- name of the person with his/her designation underneath and email address
5-contact number
6- 1-800--- number with the extension number

its up to the designer how he/she places the details,but it must look professional

Industry/Entity Type

Business

Contact Information for Business Card

5-contact number

Requirements
Must have
• 1- logo on front and underneath the logo there should be a line saying
• "Cleaner . Cheaper . Power"
• 2-website i.e "www.halvexpowerco.com"
• 3- Icons for Facebook and Instagram that tells the clients we are available on both social sites.
• 4- name of the person with his/her designation underneath and email address
• 5-contact number of the person
• 6- 1-800--- number with the extension number
• 7-card should be in black shade like the logo

```html
<!DOCTYPE html>
<html lang="en">
<head>
<meta charset="utf-8">
<title>Halvex Power — Business Card</title>
<link rel="stylesheet" href="https://fonts.googleapis.com/css2?family=Open+Sans:wght@400;600;700&display=swap">
<style>
  :root {
    --page: #e9e7e4;
    --card: #161616;
    --card-edge: #0d0d0d;
    --green: #7ac143;
    --grey: #8c8c8c;
    --light: #f1f1f1;
    --rule: #5a5a5a;
  }
  * { box-sizing: border-box; margin: 0; padding: 0; }
  html, body { width: 1200px; height: 864px; overflow: hidden; }
  body {
    background: var(--page);
    font-family: "Open Sans", Arial, sans-serif;
    display: flex;
    align-items: center;
    justify-content: center;
    gap: 48px;
  }
  .card {
    width: 532px;
    height: 304px;
    background: var(--card);
    border: 1px solid var(--card-edge);
    box-shadow: 0 10px 24px rgba(0,0,0,.25);
    position: relative;
    color: var(--light);
  }
  /* Front */
  .card-front .brand {
    position: absolute;
    top: 96px;
    left: 0; right: 0;
    text-align: center;
    font-size: 40px;
    font-weight: 700;
    line-height: 1.2;
    color: var(--green);
    letter-spacing: .5px;
  }
  .card-front .tagline {
    position: absolute;
    top: 150px;
    left: 0; right: 0;
    text-align: center;
    font-size: 13px;
    font-weight: 600;
    letter-spacing: 2px;
    color: var(--light);
  }
  .card-front .website {
    position: absolute;
    top: 208px;
    left: 0; right: 0;
    text-align: center;
    font-size: 13px;
    letter-spacing: 4px;
    color: var(--grey);
  }
  /* Back */
  .card-back .brand {
    position: absolute;
    left: 30px;
    top: 124px;
    width: 190px;
    font-size: 30px;
    font-weight: 700;
    color: var(--green);
    line-height: 1.1;
  }
  .card-back .divider {
    position: absolute;
    left: 220px;
    top: 96px;
    width: 1px;
    height: 120px;
    background: var(--rule);
  }
  .card-back .details {
    position: absolute;
    left: 238px;
    top: 104px;
  }
  .person-name {
    font-size: 18px;
    font-weight: 700;
    color: var(--green);
    line-height: 1.1;
  }
  .person-title {
    font-size: 13px;
    color: var(--grey);
    letter-spacing: .5px;
    margin-bottom: 12px;
  }
  .contact-list { list-style: none; }
  .contact-list li {
    display: flex;
    align-items: center;
    gap: 8px;
    font-size: 14px;
    line-height: 20px;
    white-space: nowrap;
  }
  .contact-list svg { width: 12px; height: 12px; fill: var(--green); flex: none; }
  .social {
    position: absolute;
    right: 18px;
    top: 104px;
    display: flex;
    gap: 4px;
  }
  .social span {
    width: 14px; height: 14px;
    background: var(--green);
    border-radius: 2px;
  }
</style>
</head>
<body>
  <section class="card card-front" aria-label="Card front">
    <div class="brand">Halvex Power</div>
    <div class="tagline">Cleaner . Cheaper . Power</div>
    <div class="website">www.halvexpowerco.com</div>
  </section>

  <section class="card card-back" aria-label="Card back">
    <div class="brand">Halvex Power</div>
    <div class="divider"></div>
    <div class="social" aria-label="Social media"><span></span><span></span></div>
    <div class="details">
      <div class="person-name">MARCUS PELL</div>
      <div class="person-title">PRESIDENT</div>
      <ul class="contact-list">
        <li>
          <svg viewBox="0 0 24 24" aria-hidden="true"><path d="M6.6 10.8a15 15 0 0 0 6.6 6.6l2.2-2.2c.3-.3.7-.4 1-.2 1.1.4 2.3.6 3.6.6.6 0 1 .4 1 1V20c0 .6-.4 1-1 1A17 17 0 0 1 3 4c0-.6.4-1 1-1h3.5c.6 0 1 .4 1 1 0 1.3.2 2.5.6 3.6.1.3 0 .7-.2 1z"/></svg>
          1-800-4410-7721 Ext. 204
        </li>
        <li>
          <svg viewBox="0 0 24 24" aria-hidden="true"><path d="M2 5h20v14H2z M4 7v.5l8 5 8-5V7l-8 5z" fill-rule="evenodd"/></svg>
          marcus@halvexpowerco.com
        </li>
        <li>
          <svg viewBox="0 0 24 24" aria-hidden="true"><circle cx="12" cy="12" r="10"/></svg>
          www.halvexpowerco.com
        </li>
      </ul>
    </div>
  </section>
</body>
</html>
```